Business Card Design for Occupational Medicine Start Up Company

We need to design a professional business card. We are a healthcare company providing occupational medicine services to blue collar industries. We are professional, efficient and high quality service providers.

Target Market(s)

Blue Collar Industry: Shipbuilding, Ports, Trucking Companies; The Executives and Safety Officers for these companies

Industry/Entity Type

Healthcare

Contact Information for Business Card

Logo, Name, Title, Email, Phone

Other font styles liked:
• Please match our Brand Guide

Requirements
Must have
• Our Company Colors and Logo

```html
<!DOCTYPE html>
<html lang="en">
<head>
<meta charset="utf-8">
<title>Crewwell Clinics – Business Card</title>
<link rel="stylesheet" href="https://fonts.googleapis.com/css2?family=Montserrat:wght@600&family=Open+Sans:wght@400;700&display=swap">
<style>
  :root {
    --navy: #29357f;
    --sky: #26a6df;
    --amber: #f6b24f;
    --ink: #111111;
    --paper: #ffffff;
    --edge: #d4d4d4;
  }
  * { box-sizing: border-box; margin: 0; padding: 0; }
  html, body { width: 1200px; height: 1200px; overflow: hidden; background: var(--paper); }
  .sheet { position: relative; width: 1200px; height: 1200px; }
  .card {
    position: absolute; top: 453px; width: 516px; height: 294px;
  }
  .card-front { left: 64px; background: var(--paper); border: 1px solid var(--edge); }
  .card-back { left: 620px; background: var(--navy); }

  .brand { position: absolute; display: flex; align-items: center; gap: 12px; }
  .brand-dot { width: 44px; height: 44px; border-radius: 50%; flex: none; }
  .brand-name {
    font-family: "Montserrat", sans-serif; font-weight: 600;
    text-transform: uppercase; line-height: 1.05; letter-spacing: 0.02em;
  }
  .brand-name span { display: block; }
  .brand-name .sub { letter-spacing: 0.3em; font-size: 0.55em; text-align: center; }

  .card-front .brand { left: 26px; top: 46px; }
  .card-front .brand-dot { background: var(--sky); }
  .card-front .brand-name { color: var(--navy); font-size: 25px; }

  .card-back .brand { left: 0; right: 0; top: 78px; flex-direction: column; gap: 14px; }
  .card-back .brand-dot { width: 64px; height: 64px; background: var(--amber); }
  .card-back .brand-name { color: var(--paper); font-size: 28px; text-align: center; }

  .person { position: absolute; left: 26px; top: 143px; font-family: "Open Sans", sans-serif; color: var(--ink); }
  .person-name { font-size: 31px; line-height: 1; font-weight: 400; }
  .person-name b { font-weight: 700; }
  .person-title { font-size: 15px; margin-top: 2px; }
  .contacts { list-style: none; margin-top: 14px; font-size: 15px; }
  .contacts li { display: flex; align-items: center; gap: 6px; line-height: 20px; }
  .contacts svg { width: 11px; height: 11px; flex: none; }
  .contacts b { font-weight: 700; }

  .stripe { position: absolute; top: 0; bottom: 0; width: 12.5px; }
  .stripe-sky { left: 437px; background: var(--sky); }
  .stripe-navy { left: 459px; background: var(--navy); }
  .stripe-amber { left: 481px; background: var(--amber); }
</style>
</head>
<body>
<main class="sheet">
  <section class="card card-front" aria-label="Business card front">
    <div class="brand">
      <div class="brand-dot"></div>
      <div class="brand-name"><span>Crewwell</span><span class="sub">Clinics</span></div>
    </div>
    <div class="person">
      <h1 class="person-name"><b>Dara</b> Holt</h1>
      <p class="person-title">Managing Director</p>
      <ul class="contacts">
        <li>
          <svg viewBox="0 0 11 11" aria-hidden="true"><rect width="11" height="11" fill="var(--navy)"/><rect x="2.5" y="3.5" width="6" height="4" fill="none" stroke="#fff" stroke-width="0.9"/><path d="M2.5 3.5 L5.5 6 L8.5 3.5" fill="none" stroke="#fff" stroke-width="0.9"/></svg>
          daraholt@mailbox.com
        </li>
        <li>
          <svg viewBox="0 0 11 11" aria-hidden="true"><rect width="11" height="11" fill="var(--navy)"/><path d="M3 2.5 L4.3 2.5 L4.8 4.3 L4 5 Q4.8 6.6 6 7 L6.7 6.2 L8.5 6.7 L8.5 8 Q5 8.5 3 4.5 Z" fill="#fff"/></svg>
          www.<b>crewwell</b>.com
        </li>
      </ul>
    </div>
    <div class="stripe stripe-sky"></div>
    <div class="stripe stripe-navy"></div>
    <div class="stripe stripe-amber"></div>
  </section>

  <section class="card card-back" aria-label="Business card back">
    <div class="brand">
      <div class="brand-dot"></div>
      <div class="brand-name"><span>Crewwell</span><span class="sub">Clinics</span></div>
    </div>
  </section>
</main>
</body>
</html>
```